Bramblewood Joinery Website

My client Bramblewood Joinery is looking for a redesign for a Word Press Website. Their current site is at www.bramblewoodjoinery.example They are a custom cabinet company, but also create bathroom, living room, bar and entertainment and bedroom cabinets too. They would like a design that emulates the master craftsman work they do yet a contemporary style.

Their current site was designed using Flash elements.

Target Market(s)

Home owners and builders of high end homes

Industry/Entity Type

Entertainment

Font styles to use
Serif
Decorative

Requirements
Must have
• Must show their work and logo using a contemporary style.
Nice to have
• Sliders that showcase their projects.

```html
<!DOCTYPE html>
<html lang="en">
<head>
<meta charset="utf-8">
<title>Bramblewood Joinery</title>
<link href="https://fonts.googleapis.com/css2?family=Cabin:wght@400;500&display=swap" rel="stylesheet">
<style>
:root{
  --bg:#1b1b1b;
  --green:#3cb43c;
  --green-dark:#1f5a22;
  --green-pale:#cdeecb;
  --white:#ffffff;
  --ink:#2a2a2a;
}
*{margin:0;padding:0;box-sizing:border-box}
html,body{width:1193px;height:1200px;overflow:hidden}
body{background:var(--bg);font-family:'Cabin',sans-serif;position:relative;
  background-image:repeating-linear-gradient(45deg,#202020 0 2px,#181818 2px 4px)}
.abs{position:absolute}
.hero{left:0;top:108px;width:1193px;height:506px;
  background:linear-gradient(135deg,#b89a74 0%,#e2cfae 35%,#c9a879 60%,#8a6a4a 100%)}
.header-top{left:60px;top:37px;width:1074px;height:48px;background:var(--white)}
.brand{left:82px;top:50px;display:flex;align-items:center;gap:8px;color:var(--green);font-size:17px;font-weight:500}
.brand-dot{width:14px;height:14px;border-radius:50%;background:var(--green)}
.tagline{right:84px;top:52px;color:var(--green);font-size:14.5px}
.nav{left:50px;top:85px;width:1093px;height:55px;background:var(--green);display:flex;align-items:center;padding-left:212px;gap:28px}
.nav a{color:var(--white);text-decoration:none;font-size:14px}
.caption{left:156px;color:var(--ink)}
.caption-title{top:379px;width:372px;height:59px;background:rgba(255,255,255,.72);font-size:37px;padding:5px 0 0 30px}
.caption-sub{top:439px;width:344px;height:37px;background:rgba(255,255,255,.72);font-size:24px;padding:2px 0 0 35px}
.dots{left:553px;top:578px;display:flex;gap:7px}
.dots span{width:11px;height:11px;background:rgba(255,255,255,.85)}
.dots span.on{background:#333;border:2px solid #fff}
.social{left:1143px;display:flex;flex-direction:column;gap:12px;top:202px}
.social span{width:34px;height:34px;border-radius:6px;background:#5d7fb8}
.social span:nth-child(2){background:#4ab3d8}
.social span:nth-child(3){background:#d15b5b}
.welcome{left:50px;top:614px;width:1093px;height:164px;background:var(--green);text-align:center;color:var(--white)}
.welcome h1{font-weight:400;font-size:33px;margin-top:14px}
.welcome p{font-size:13px;line-height:18.5px;width:960px;margin:10px auto 0}
.btn{display:inline-block;margin-top:11px;width:128px;height:37px;line-height:37px;background:var(--green-dark);font-size:15.5px}
.content{left:60px;top:778px;width:1074px;height:328px;background:var(--white)}
.label{color:var(--green);font-size:16px;top:789px}
.works-img{left:60px;top:812px;width:655px;height:274px;background:linear-gradient(160deg,#cfc8bd,#8b8275 55%,#2f2a26)}
.video-img{left:722px;top:812px;width:412px;height:274px;background:linear-gradient(160deg,#8f877c,#bcb3a6 45%,#2b2622)}
.menu{left:60px;top:812px}
.menu li{list-style:none;height:38.6px;line-height:38.6px;padding-left:37px;font-size:15.5px;color:var(--green);position:relative;z-index:2}
.menu li::before{content:"";position:absolute;left:23px;top:15px;border-left:5px solid currentColor;border-top:4px solid transparent;border-bottom:4px solid transparent}
.menu li.active{color:var(--white)}
.footer{left:50px;top:1106px;width:1093px;height:55px;background:var(--green);color:var(--white);font-size:11.5px;display:flex;align-items:center;padding:0 26px}
.footer nav{display:flex;gap:23px}
.footer .copy{margin-left:auto;padding-right:14px}
</style>
</head>
<body>
<div class="abs hero" role="img" aria-label="Photo of a traditional cream kitchen with chandelier, range hood and flowers"></div>
<div class="abs header-top"></div>
<div class="abs brand"><span class="brand-dot"></span>Bramblewood Joinery</div>
<div class="abs tagline">Kansas City's Premier Custom Kitchen Cabinet Design Company</div>
<nav class="abs nav">
  <a href="#">Home</a><a href="#">Who We Are</a><a href="#">Getting Started</a><a href="#">Contact Us</a><a href="#">Customer Experience</a><a href="#">Professional</a><a href="#">Portfolio</a><a href="#">Cabinet Hardware</a>
</nav>
<div class="abs caption caption-title">Customizable Theme</div>
<div class="abs caption caption-sub">Contrary to popular belief</div>
<div class="abs dots"><span></span><span></span><span></span><span class="on"></span><span></span></div>
<div class="abs social"><span></span><span></span><span></span></div>

<section class="abs welcome">
  <h1>Welcome To Our Website</h1>
  <p>At Bramblewood Joinery, we've been designing and manufacturing the Midwest's finest custom cabinets and fixtures since 1966. From single cabinets to room remodels to entire home installations, our expert artisans help turn the house you live in to the home you've always dreamed of.</p>
  <span class="btn">Read More</span>
</section>

<div class="abs content"></div>
<div class="abs label" style="left:77px">Our Works</div>
<div class="abs label" style="left:730px">Our Video</div>
<div class="abs works-img" role="img" aria-label="Photo of a white kitchen with island and pendant lights"></div>
<div class="abs video-img" role="img" aria-label="Video still of a white kitchen with steel refrigerator"></div>
<svg class="abs" style="left:0;top:0" width="1193" height="1200" viewBox="0 0 1193 1200">
  <polygon points="60,851 213,851 321,970 218,1088 60,1088" fill="#cdeecb"/>
  <polygon points="60,812 177,812 213,851 60,851" fill="#3cb43c"/>
  <g stroke="#ffffff" stroke-width="1.2">
    <line x1="60" y1="889.6" x2="248" y2="889.6"/>
    <line x1="60" y1="928.2" x2="283" y2="928.2"/>
    <line x1="60" y1="966.8" x2="318" y2="966.8"/>
    <line x1="60" y1="1005.4" x2="292" y2="1005.4"/>
    <line x1="60" y1="1044" x2="258" y2="1044"/>
  </g>
  <circle cx="918" cy="946" r="32" fill="#1a1a1a" opacity=".85"/>
  <polygon points="909,929 930,946 909,963" fill="#ffffff"/>
</svg>
<ul class="abs menu">
  <li class="active">Kitchens</li><li>Bath</li><li>Office</li><li>Closet / Dressing</li><li>Workshop</li><li>Entertainment</li><li>PhotoGallery</li>
</ul>

<footer class="abs footer">
  <nav><span>Home</span><span>Who We Are</span><span>Getting Started</span><span>Contact Us</span><span>Customer Experience</span><span>Professional</span><span>Portfolio</span><span>Cabinet Hardware</span></nav>
  <span class="copy">© 2014.www.bramblewoodjoinery.example</span>
</footer>
</body>
</html>
```